Brookvale Estates LLC stationary for a real estate property management company.

Create stationary (letterhead, envelopes, business cards) using Brookvale Estates LLC logo as primary creative element. Stationary design needs to be horizontal, leaving as much space as possible for correspondence copy. See attached Creative Brief and past stationary files for details.

Target Market(s)

Prospective apartment residents and current residents, vendors, and government agencies.

Industry/Entity Type

Property Management

Contact Information for Business Card

Business card employee title: Property Manager. Should include address, phone, fax, email, website, slogan, and Brookvale Estates logo.

Font styles to use
Sans Serif

Colors
0592cd
000000

Requirements
Must have
• Tone should be conservative, institutional, business (i.e. banking, finance, real estate). Must include: address, phone, fax, website, and slogan (see attached Creative Brief). Should be a horizontal design, leaving as much room as possible for letter correspondence copy.
Nice to have
• Please use an Arial or Helvetica style font.
Should not have
• Letterhead layout should leave as much room as possible for copy.

```html
<!DOCTYPE html>
<html lang="en">
<head>
<meta charset="utf-8">
<title>Brookvale Estates LLC – Business Card</title>
<link href="https://fonts.googleapis.com/css2?family=Arimo:wght@400;700&display=swap" rel="stylesheet">
<style>
  :root {
    --page-bg: #e6e4e1;
    --brand-blue: #0a67a3;
    --logo-blue: #1b6fb0;
    --card-white: #f4f4f4;
    --swoosh-grey: #45464a;
    --back-light: #7b7b7e;
    --back-dark: #47474a;
    --text-white: #ffffff;
  }
  * { margin: 0; padding: 0; box-sizing: border-box; }
  html, body {
    width: 1200px; height: 960px; overflow: hidden;
    background: var(--page-bg);
    font-family: "Arimo", Arial, Helvetica, sans-serif;
  }
  .card {
    position: absolute;
    width: 600px; height: 341px;
    overflow: hidden;
    box-shadow: 0 3px 8px rgba(0,0,0,0.25);
  }
  .card-front { left: 302px; top: 130px; background: var(--brand-blue); }
  .card-back {
    left: 300px; top: 489px;
    background: linear-gradient(135deg, var(--back-light) 0%, var(--back-dark) 45%, var(--back-dark) 100%);
  }
  .front-shapes { position: absolute; inset: 0; }
  .contact-block {
    position: absolute; left: 24px; top: 84px;
    color: var(--text-white);
  }
  .person-name { font-size: 21px; font-weight: 700; letter-spacing: 0.2px; line-height: 1.1; }
  .person-title { font-size: 15px; margin-top: 3px; }
  .address { font-size: 13.5px; line-height: 19px; margin-top: 14px; }
  .contact-list { list-style: none; margin-top: 12px; font-size: 13.5px; }
  .contact-list li { display: flex; align-items: center; height: 19.5px; }
  .contact-list svg { width: 13px; height: 13px; margin-right: 10px; fill: var(--text-white); flex: none; }
  .front-brand {
    position: absolute; left: 322px; top: 162px; width: 270px;
    text-align: center;
    color: var(--logo-blue);
    font-size: 22px; font-weight: 700; letter-spacing: 0.5px;
    text-transform: uppercase;
  }
  .back-brand {
    position: absolute; left: 0; right: 0; top: 152px;
    text-align: center; color: var(--text-white);
    font-size: 32px; font-weight: 700; letter-spacing: 1px;
    text-transform: uppercase;
  }
  .slogan {
    position: absolute; left: 0; right: 0; top: 285px;
    text-align: center; color: var(--text-white);
    font-size: 16.5px; font-weight: 700;
  }
</style>
</head>
<body>

<section class="card card-front">
  <svg class="front-shapes" width="600" height="341" viewBox="0 0 600 341" aria-hidden="true">
    <path d="M366 -30 C 270 40, 250 250, 372 341 L 362 341 C 232 250, 250 30, 352 -30 Z" fill="var(--swoosh-grey)"/>
    <path d="M300 40 C 380 -10, 500 -10, 552 30 C 490 0, 380 0, 300 40 Z" fill="var(--swoosh-grey)"/>
    <path d="M389 0 A180 180 0 0 0 368 341 L600 341 L600 0 Z" fill="var(--text-white)"/>
    <path d="M394 0 A176 176 0 0 0 373 341 L600 341 L600 0 Z" fill="var(--card-white)"/>
  </svg>

  <div class="contact-block">
    <div class="person-name">DANIEL REYES</div>
    <div class="person-title">Property Manager</div>
    <div class="address">2680 Harbor Ridge Drive #B210<br>Carlsbad, CA 92008</div>
    <ul class="contact-list">
      <li><svg viewBox="0 0 16 16"><path d="M3.5 1l2.5 3-1.5 2c1 2 3 4 5 5l2-1.5 3 2.5-1.5 2.5C8 15 1 8 1 2.5z"/></svg>760-555-0142</li>
      <li><svg viewBox="0 0 16 16"><path d="M4 1h8v4H4zM1 6h14v6h-3v3H4v-3H1zm4 4v4h6v-4z"/></svg>760-555-0187</li>
      <li><svg viewBox="0 0 16 16"><path d="M1 3h14v10H1zm1.5 1.5v.5L8 9l5.5-4v-.5zM2.5 6.5v5h11v-5L8 10.5z"/></svg>daniel@brookvaleestates.us</li>
      <li><svg viewBox="0 0 16 16"><path d="M8 1a7 7 0 1 0 0 14A7 7 0 0 0 8 1zm0 1.5c.8 1 1.4 2.3 1.6 3.5H6.4C6.6 4.8 7.2 3.5 8 2.5zM2.7 9.5a5.6 5.6 0 0 1 0-3H5a11 11 0 0 0 0 3zm.6 1.5h2c.3 1.2.8 2.3 1.4 3.2A5.5 5.5 0 0 1 3.3 11zM8 13.5c-.8-1-1.4-2.3-1.6-2.5h3.2c-.2.2-.8 1.5-1.6 2.5zm1.7-4H6.3a9 9 0 0 1 0-3h3.4a9 9 0 0 1 0 3zm.6 4.7c.6-.9 1.1-2 1.4-3.2h2a5.5 5.5 0 0 1-3.4 3.2zM11 9.5a11 11 0 0 0 0-3h2.3a5.6 5.6 0 0 1 0 3z"/></svg>www.brookvaleestates.us</li>
    </ul>
  </div>

  <div class="front-brand">Brookvale Estates LLC</div>
</section>

<section class="card card-back">
  <div class="back-brand">Brookvale Estates</div>
  <div class="slogan">Multifamily Property Management</div>
</section>

</body>
</html>
```